CM Candle Tube Packaging Design

Website: www.corvelmare.example
IG: @corvel.mare
Tagline: Elevate Your Ambiance
My brand is a sophisticated brand with luxury candles made of coconut wax. Im looking for an upscale minimalist chic design.
Discover the transformative power of positive energy with Corvel Mare candles. Indulge in true luxury with our specially crafted coconut wax blend that not only ignites captivating scents but also embodies modern elegance and empowering elements.
At Corvel Mare we're committed to delivering a unique and exhilarating aromatic experience to all candle lovers. Each candle is meticulously handcrafted in small batches using luxury fragrance oils exclusively formulated for coconut wax.
Our candles are:
Clean-burning
Paraben-Free
Phthalate-Free
Skin-Safe
Pet-Friendly

```html
<!DOCTYPE html>
<html lang="en">
<head>
<meta charset="utf-8">
<title>Corvel Mare — Candle Tube Packaging</title>
<link rel="stylesheet" href="https://fonts.googleapis.com/css2?family=Josefin+Sans:wght@200;300&family=Montserrat:wght@400;500&family=Poppins:ital,wght@1,400&family=Homemade+Apple&display=swap">
<style>
  :root {
    --backdrop: #f1e2e4;
    --blush: #e6b8b5;
    --blush-deep: #dcaaa8;
    --cream: #f4ece8;
    --lid-rim: #efc9c9;
    --ink: #1c1718;
  }
  * { margin: 0; padding: 0; box-sizing: border-box; }
  html, body { width: 1200px; height: 1107px; overflow: hidden; background: var(--backdrop); }
  .canvas { position: relative; width: 1200px; height: 1107px; }

  .tube-wrap {
    position: absolute; left: 110px; top: 140px; width: 450px; height: 860px;
    background: linear-gradient(90deg, #efbfbc 0%, var(--blush) 45%, var(--blush-deep) 100%);
    overflow: hidden; color: var(--ink); text-align: center;
  }
  .flame-art { position: absolute; left: 0; top: 0; width: 450px; height: 860px; }
  .lid-seam { position: absolute; left: 0; right: 0; top: 250px; height: 1px; background: rgba(255,255,255,0.6); }
  .website {
    position: absolute; left: 0; right: 0; top: 205px;
    font: 400 14px/1 "Montserrat", sans-serif; letter-spacing: 0.5px;
  }
  .wordmark {
    position: absolute; left: 0; right: 0; top: 440px;
    font: 200 48px/1 "Josefin Sans", sans-serif; letter-spacing: 1px;
    transform: scaleY(1.15);
  }
  .product-line {
    position: absolute; left: 0; right: 0; top: 515px;
    display: flex; align-items: center; justify-content: center; gap: 14px;
    font: 500 14px/1 "Montserrat", sans-serif; letter-spacing: 5px;
  }
  .product-line .rule { width: 20px; height: 1px; background: var(--ink); }
  .signature {
    position: absolute; left: 0; right: 0; top: 545px;
    font: 400 11px/1.6 "Homemade Apple", cursive;
  }
  .tagline {
    position: absolute; left: 0; right: 0; top: 712px;
    font: italic 400 18px/1 "Poppins", sans-serif;
  }
  .net-weight {
    position: absolute; left: 0; right: 0; top: 795px;
    font: 400 14px/1 "Montserrat", sans-serif;
  }

  .lid {
    position: absolute; left: 645px; top: 395px; width: 430px; height: 430px;
    border-radius: 50%; background: var(--lid-rim);
    display: flex; align-items: center; justify-content: center;
  }
  .lid-face {
    width: 390px; height: 390px; border-radius: 50%;
    background: radial-gradient(circle at 40% 40%, #e8bcba, var(--blush));
    display: flex; align-items: center; justify-content: center;
  }
  .lid-monogram {
    font: 300 72px/1 "Josefin Sans", sans-serif; color: var(--ink); letter-spacing: 2px;
  }
</style>
</head>
<body>
<main class="canvas">
  <section class="tube-wrap">
    <svg class="flame-art" viewBox="0 0 450 860" role="img" aria-label="Large stylised flame artwork in cream and blush sweeping up the right side of the wrap">
      <defs>
        <linearGradient id="flameTone" x1="0" y1="0" x2="1" y2="1">
          <stop offset="0" stop-color="#f4ece8"/>
          <stop offset="1" stop-color="#ead6d2"/>
        </linearGradient>
      </defs>
      <path d="M450 0 L450 860 L250 860 C200 700 220 520 330 330 C380 240 420 130 450 0 Z" fill="url(#flameTone)"/>
    </svg>
    <div class="lid-seam"></div>
    <p class="website">www.corvelmare.example</p>
    <h1 class="wordmark">CORVEL MARE</h1>
    <p class="product-line"><span class="rule"></span>HANDMADE CANDLES<span class="rule"></span></p>
    <p class="signature">with purpose and love</p>
    <p class="tagline">Elevate Your Ambiance</p>
    <p class="net-weight">9 OZ/255G</p>
  </section>

  <section class="lid">
    <div class="lid-face">
      <span class="lid-monogram">CM</span>
    </div>
  </section>
</main>
</body>
</html>
```